Need a stunning home page for Car rental company

For a client, I need a slick and sumber home page design. It is a small, local car rental company, with a handful of cars available for rent.
Selling points: affordable lease, availability, always clean cars
The design should be:
- flat and modern
- no, or very few animations/sliders
- CTA: booking form for renting a car.
- 3 featured cars with images and facts (see website) with button to read more about the car.
- fullscreen background video can be an option
- main colour: #efba01
The site is under construction here:
http://solvikutleie.hammerlia.no/
Delivery requirements:
I need a layered & well organised PSD file delivered.

```html
<!DOCTYPE html>
<html lang="en">
<head>
<meta charset="utf-8">
<title>Solvikutleie – Car Rental</title>
<link rel="stylesheet" href="https://fonts.googleapis.com/css2?family=Open+Sans:wght@400;600;700&display=swap">
<style>
:root{
  --brand:#efba01;
  --brand-dark:#e0a800;
  --orange:#f07c10;
  --orange-light:#f5a020;
  --ink:#444;
  --ink-soft:#555;
  --muted:#777;
  --line:#dcdcdc;
  --card:#f2f2f2;
  --white:#fff;
  --green:#6a9a1f;
}
*{box-sizing:border-box;margin:0;padding:0}
html,body{width:822px;height:1200px;overflow:hidden}
body{font-family:"Open Sans",Arial,sans-serif;color:var(--ink);background:var(--white);position:relative}
.abs{position:absolute}
.top-rule{left:0;top:0;width:822px;height:2px;background:var(--brand)}
.site-header{left:0;top:2px;width:822px;height:75px;border-bottom:1px solid var(--brand)}
.brand-name{left:84px;top:27px;font-size:22px;font-weight:700;letter-spacing:1px;color:var(--ink-soft)}
.main-nav{left:350px;top:34px;display:flex;gap:15px;font-size:10.5px;color:var(--ink-soft)}
.hero{left:0;top:77px;width:822px;height:309px;background:linear-gradient(100deg,#f2a12a 0%,#c8612a 18%,#3b3e62 45%,#1b2648 70%,#0f1730 100%);border-bottom:3px solid var(--brand)}
.hero-title{left:430px;top:184px;font-size:24px;font-weight:700;color:var(--white)}
.hero-text{left:431px;top:221px;width:285px;font-size:9.5px;line-height:13px;color:var(--white);text-align:justify}
.hero-link{left:639px;top:256px;font-size:10px;font-weight:600;color:var(--brand);display:flex;align-items:center;gap:6px}
.hero-cars{left:440px;top:320px;width:304px;height:108px;border-radius:40px 60px 20px 20px;background:linear-gradient(90deg,#222 0%,#444 40%,#c42020 55%,#e03030 100%)}
.hero-dots{left:752px;top:335px;display:flex;flex-direction:column;gap:8px}
.hero-dots span{width:6px;height:6px;border-radius:50%;background:var(--brand)}
.hero-dots span:first-child{background:var(--white)}
.play-link{left:472px;top:431px;font-size:10px;font-weight:600;color:var(--green);display:flex;align-items:center;gap:6px}
.booking{left:102px;top:189px;width:302px;height:297px;background:var(--white);border:1px solid #e2e2e2;border-top:3px solid var(--brand)}
.tab{top:0;height:30px;font-size:11px;display:flex;align-items:center;justify-content:center}
.tab-book{left:0;width:143px;color:var(--brand);background:var(--white);top:3px}
.tab-manage{left:143px;width:158px;color:var(--white);background:var(--brand);height:33px}
.lbl{font-size:7.5px;color:var(--ink-soft);text-transform:uppercase}
.field{border:1px solid var(--line);border-radius:2px;background:var(--white);font-size:8.5px;color:#999;display:flex;align-items:center;padding-left:8px}
.check{left:25px;top:100px;font-size:7.5px;color:var(--ink-soft);display:flex;align-items:center;gap:6px}
.check i{width:8px;height:8px;border:1px solid #ccc;display:block}
.btn-continue{left:173px;top:196px;width:105px;height:29px;border-radius:2px;background:var(--brand);color:var(--white);font-size:12px;display:flex;align-items:center;justify-content:center;gap:6px}
.btn-book{left:26px;top:238px;width:251px;height:37px;border-radius:2px;background:linear-gradient(var(--orange-light),var(--orange));color:var(--white);text-align:center}
.btn-book b{display:block;font-weight:400;font-size:15px;line-height:18px;margin-top:3px}
.btn-book small{display:block;font-size:7px}
.divider{left:78px;top:494px;width:666px;border-top:1px dashed #ccc}
.intro-title{left:91px;top:509px;width:190px;font-size:11.5px;line-height:13.5px;text-align:justify}
.intro-text{left:91px;top:547px;width:190px;font-size:9px;line-height:12.5px;text-align:justify;color:var(--ink-soft)}
.more{font-size:9.5px;font-weight:600;color:var(--ink-soft);display:flex;align-items:center;gap:8px}
.feature h3{font-size:11.5px;font-weight:400;display:flex;align-items:center;gap:6px;color:var(--ink)}
.feature p{margin:8px 0 0 5px;width:190px;font-size:9px;line-height:12.5px;text-align:justify;color:var(--ink-soft)}
.section-title{left:98px;top:708px;font-size:14px;font-weight:600;color:var(--ink-soft)}
.car-card{top:742px;width:190px;height:331px;background:var(--card)}
.car-photo{width:190px;height:122px;border-bottom:3px solid var(--brand)}
.car-card h4{margin:10px 0 0 10px;font-size:9.5px;font-weight:400;text-transform:uppercase}
.specs{margin:8px 0 0 10px;font-size:9px;border-collapse:collapse}
.specs td{height:20.5px;color:var(--ink-soft)}
.specs td:first-child{width:103px}
.btn-more{display:inline-block;margin:5px 0 0 10px;padding:5px 8px;background:var(--brand);border-radius:2px;font-size:9px;color:var(--ink-soft);text-transform:uppercase}
.site-footer{left:0;top:1090px;width:822px;height:110px;background:var(--brand)}
.foot-nav{left:0;top:16px;width:822px;display:flex;justify-content:center;gap:15px;font-size:10px;color:var(--white)}
.social{left:347px;top:45px;display:flex;gap:16px}
.social span{width:20px;height:20px;border-radius:2px;background:#3a6ab0}
.copyright{left:0;top:82px;width:822px;text-align:center;font-size:8.5px;color:var(--white)}
.foot-rule{left:0;top:104px;width:822px;height:1px;background:var(--white)}
</style>
</head>
<body>
<div class="abs top-rule"></div>
<header class="abs site-header">
  <div class="abs brand-name">SOLVIKUTLEIE</div>
  <nav class="abs main-nav"><span>Home</span><span>Our Fleet</span><span>Services</span><span>Contact Us</span><span>Blog</span><span>Page Templates</span><span>About Us</span></nav>
</header>

<section class="abs hero" role="img" aria-label="Photo of a dark blue car against an orange sunset sky"></section>
<h1 class="abs hero-title">Great car hire deals</h1>
<p class="abs hero-text">Phasellus eget ultricies libero.Sed dolor turpis,malesuada vitae cursus a,auctor semper neque.</p>
<div class="abs hero-link"><svg width="10" height="10" viewBox="0 0 10 10"><circle cx="5" cy="5" r="4.3" fill="none" stroke="#efba01"/><path d="M3 5h4M5.5 3.5L7 5 5.5 6.5" stroke="#efba01" fill="none"/></svg>Learn More</div>
<div class="abs hero-cars" role="img" aria-label="Photo of a black hatchback and a red coupe with a video play button"></div>
<div class="abs hero-dots"><span></span><span></span><span></span></div>
<div class="abs play-link"><svg width="16" height="16" viewBox="0 0 16 16"><circle cx="8" cy="8" r="8" fill="#6a9a1f"/><path d="M6 4.5l5 3.5-5 3.5z" fill="#fff"/></svg>Play Now How it works</div>

<form class="abs booking">
  <div class="abs tab tab-book">Book a Car</div>
  <div class="abs tab tab-manage">Manage Reservation</div>
  <div class="abs lbl" style="left:25px;top:44px">Location</div>
  <div class="abs field" style="left:22px;top:61px;width:257px;height:29px">Enter City or Zip code</div>
  <div class="abs check"><i></i>Return at different location</div>
  <div class="abs lbl" style="left:25px;top:124px">Pick-up date</div>
  <div class="abs lbl" style="left:165px;top:124px">Drop-off date</div>
  <div class="abs field" style="left:22px;top:139px;width:78px;height:29px"><svg width="10" height="10" viewBox="0 0 10 10"><rect x="0.5" y="1.5" width="9" height="8" fill="none" stroke="#999"/><path d="M0.5 3.5h9M3 5.5h1M5 5.5h1M7 5.5h1M3 7.5h1M5 7.5h1" stroke="#999"/></svg></div>
  <div class="abs field" style="left:106px;top:139px;width:34px;height:29px"></div>
  <div class="abs field" style="left:162px;top:139px;width:78px;height:29px"><svg width="10" height="10" viewBox="0 0 10 10"><rect x="0.5" y="1.5" width="9" height="8" fill="none" stroke="#999"/><path d="M0.5 3.5h9M3 5.5h1M5 5.5h1M7 5.5h1M3 7.5h1M5 7.5h1" stroke="#999"/></svg></div>
  <div class="abs field" style="left:245px;top:139px;width:34px;height:29px"></div>
  <div class="abs lbl" style="left:25px;top:181px">Car type</div>
  <div class="abs field" style="left:22px;top:196px;width:78px;height:29px;justify-content:space-between;padding-right:8px">Standard<svg width="7" height="4"><path d="M0 0h7L3.5 4z" fill="#888"/></svg></div>
  <div class="abs btn-continue">Continue<svg width="5" height="7"><path d="M0 0l5 3.5L0 7z" fill="#fff"/></svg></div>
  <div class="abs btn-book"><b>Book Now Car for Rental</b><small>Try its FREE to first booking</small></div>
</form>

<div class="abs divider"></div>
<h2 class="abs intro-title" style="font-weight:400">We are leading car rental agency with 300,000 Happy Customers.</h2>
<p class="abs intro-text">Morbi orci ante,consectetur id vestibulum quis,suscipit eu eros.Duis non egestas dolor.Duis non volutpat leo.Aliquam nisi eros,accumsan non gravida vitae,ultrices eu eros.Phasellus sagittis mattis tristique.</p>
<div class="abs more" style="left:91px;top:619px"><svg width="10" height="10" viewBox="0 0 10 10"><circle cx="5" cy="5" r="4.3" fill="none" stroke="#888"/><path d="M3 5h4M5.5 3.5L7 5 5.5 6.5" stroke="#888" fill="none"/></svg>Learn More</div>

<div class="abs feature" style="left:306px;top:509px"><h3><svg width="11" height="11" viewBox="0 0 11 11"><path d="M1 1h4l5 5-4 4-5-5z" fill="#555"/><circle cx="3" cy="3" r="1" fill="#fff"/></svg>Special low rates on car booking</h3><p>Nunc ut nibh enim,id dapibus quam.Mauris id est at diam rutrum ultricies.Vivamus et dolor velit.Nam congue blandit nulla sed tincidunt.</p></div>
<div class="abs feature" style="left:526px;top:509px"><h3><svg width="11" height="11" viewBox="0 0 11 11"><rect x="0.5" y="1.5" width="9" height="9" fill="none" stroke="#555"/><path d="M4 7l1-2 5-5 1 1-5 5z" fill="#555"/></svg>Manage your booking online</h3><p>Nunc ut nibh enim,id dapibus quam.Mauris id est at diam rutrum ultricies.Vivamus et dolor velit.Nam congue blandit nulla sed tincidunt.</p></div>
<div class="abs feature" style="left:306px;top:605px"><h3><svg width="11" height="11" viewBox="0 0 11 11"><circle cx="5.5" cy="5.5" r="4.5" fill="none" stroke="#555" stroke-width="1.5"/><circle cx="5.5" cy="5.5" r="2" fill="none" stroke="#555"/></svg>Special low rates on car booking</h3><p>Nunc ut nibh enim,id dapibus quam.Mauris id est at diam rutrum ultricies.Vivamus et dolor velit.Nam congue blandit nulla sed tincidunt.</p></div>
<div class="abs feature" style="left:526px;top:605px"><h3><svg width="11" height="11" viewBox="0 0 11 11"><circle cx="5.5" cy="5.5" r="4.8" fill="none" stroke="#555"/><path d="M3 7l2.5-4L8 7z" fill="none" stroke="#555"/></svg>Manage your booking online</h3><p>Nunc ut nibh enim,id dapibus quam.Mauris id est at diam rutrum ultricies.Vivamus et dolor velit.Nam congue blandit nulla sed tincidunt.</p></div>

<h2 class="abs section-title">3 FEATURED CARS</h2>

<article class="abs car-card" style="left:98px">
  <div class="car-photo" role="img" aria-label="Photo of a dark blue sedan parked by a stone building" style="background:linear-gradient(180deg,#8a8a82 0%,#6b6a66 45%,#2d3058 65%,#b8b2a6 100%)"></div>
  <h4>About the car</h4>
  <table class="specs"><tr><td>Car type</td><td>Car</td></tr><tr><td>Maks. pers</td><td>2</td></tr><tr><td>Ant. Doors</td><td>4</td></tr><tr><td>Min. driver age</td><td>21</td></tr><tr><td>Gearbox</td><td>Manual</td></tr><tr><td>Air Conditioning?</td><td>yes</td></tr><tr><td>Unlimited km?</td><td>in the</td></tr></table>
  <span class="btn-more">Read more</span>
</article>
<article class="abs car-card" style="left:314px">
  <div class="car-photo" role="img" aria-label="Photo of a red sports car on a white background" style="background:radial-gradient(ellipse at 50% 45%,#d42a2a 0%,#b01818 35%,#ececec 62%,#ffffff 100%)"></div>
  <h4>About the car</h4>
  <table class="specs"><tr><td>Car type</td><td>Car</td></tr><tr><td>Maks. pers</td><td>2</td></tr><tr><td>Ant. Doors</td><td>4</td></tr><tr><td>Min. driver age</td><td>21</td></tr><tr><td>Gearbox</td><td>Manual</td></tr><tr><td>Air Conditioning?</td><td>yes</td></tr><tr><td>Unlimited km?</td><td>in the</td></tr></table>
  <span class="btn-more">Read more</span>
</article>
<article class="abs car-card" style="left:530px">
  <div class="car-photo" role="img" aria-label="Photo of a red sedan driving on a coastal road" style="background:linear-gradient(180deg,#d9c9a8 0%,#b7a98a 30%,#c42222 55%,#555 100%)"></div>
  <h4>About the car</h4>
  <table class="specs"><tr><td>Car type</td><td>Car</td></tr><tr><td>Maks. pers</td><td>2</td></tr><tr><td>Ant. Doors</td><td>4</td></tr><tr><td>Min. driver age</td><td>21</td></tr><tr><td>Gearbox</td><td>Manual</td></tr><tr><td>Air Conditioning?</td><td>yes</td></tr><tr><td>Unlimited km?</td><td>in the</td></tr></table>
  <span class="btn-more">Read more</span>
</article>

<footer class="abs site-footer">
  <nav class="abs foot-nav"><span>Home</span><span>Our Fleet</span><span>Services</span><span>Contact Us</span><span>Blog</span><span>Page Templates</span><span>About Us</span></nav>
  <div class="abs social"><span></span><span style="background:#3aa0d0"></span><span style="background:#2a6aa8"></span><span style="background:#f07c10"></span></div>
  <div class="abs copyright">© 2014.www.companyname.com</div>
  <div class="abs foot-rule"></div>
</footer>
</body>
</html>
```